Maple Roster Business Card for recruitment company

We are looking for a Business Card Design that incorporates our personal details and our busines name and logo. We are a specialized search consultancy that recruit Property and Construction professionals.
We would like a business card that stands out and is appealing to the Construction and Property industry as well.

Target Market(s)

people in the construction and property industry

Contact Information for Business Card

Business Name and logo

Font styles to use
Serif

Colors
0094D4
00A9DD
6FCCEA
C7EBF8
E9F6FB

Requirements
Must have
• Business name and logo as well as contact details
Should not have
• No photos of us please

```html
<!DOCTYPE html>
<html lang="en">
<head>
<meta charset="utf-8">
<title>Maple Roster Business Card</title>
<link rel="stylesheet" href="https://fonts.googleapis.com/css2?family=Questrial&family=Mulish:wght@700;800&display=swap">
<style>
  :root {
    --backdrop: #e4e6e8;
    --navy: #08324a;
    --navy-light: #0d4862;
    --navy-deep: #042538;
    --ink: #333a3f;
    --paper-top: #ffffff;
    --paper-bottom: #efefef;
    --white: #ffffff;
  }
  * { box-sizing: border-box; margin: 0; padding: 0; }
  html, body {
    width: 1200px; height: 732px; overflow: hidden;
    background: var(--backdrop);
  }
  .canvas { position: relative; width: 1200px; height: 732px; }
  .card {
    position: absolute; top: 242px; width: 436px; height: 249px;
    box-shadow: 0 6px 14px rgba(0,0,0,0.25);
    overflow: hidden;
  }
  .card-front {
    left: 144px;
    background: linear-gradient(160deg, var(--paper-top) 40%, var(--paper-bottom));
    font-family: "Questrial", sans-serif; color: var(--ink);
  }
  .card-back { left: 621px; }
  .brand-band {
    position: absolute; left: 0; top: 0; width: 100%; height: 55px;
    background: var(--navy);
    display: flex; align-items: center; justify-content: center;
  }
  .brand-name {
    font-family: "Questrial", sans-serif; font-size: 27px;
    letter-spacing: 0.5px; color: var(--white); text-transform: uppercase;
    line-height: 1;
  }
  .identity {
    position: absolute; right: calc(436px - 236px); top: 111px;
    text-align: right; white-space: nowrap;
  }
  .person-name {
    font-family: "Mulish", sans-serif; font-weight: 800;
    font-size: 17px; color: var(--navy); line-height: 20px;
  }
  .person-role { font-size: 12.5px; line-height: 16px; }
  .divider-vertical {
    position: absolute; left: 244px; top: 112px; width: 1px; height: 38px;
    background: var(--ink);
  }
  .contacts {
    position: absolute; left: 254px; top: 110px;
    list-style: none; font-size: 12.5px; line-height: 14.3px; white-space: nowrap;
  }
  .contacts .label {
    font-family: "Mulish", sans-serif; font-weight: 700; color: var(--navy);
    display: inline-block; width: 20px;
  }
  .divider-horizontal {
    position: absolute; left: 108px; top: 203px; width: 223px; height: 1px;
    background: var(--navy);
  }
  .location {
    position: absolute; left: 0; width: 100%; top: 215px;
    text-align: center; font-size: 12.5px; letter-spacing: 0.3px;
  }
  .back-pattern {
    position: absolute; inset: 0;
    background: linear-gradient(135deg, var(--navy-light), var(--navy-deep));
  }
  .back-brand {
    position: absolute; inset: 0;
    display: flex; align-items: center; justify-content: center;
  }
</style>
</head>
<body>
<main class="canvas">
  <section class="card card-front" aria-label="Business card front">
    <header class="brand-band">
      <span class="brand-name">Maple Roster</span>
    </header>
    <div class="identity">
      <p class="person-name">Claire Hollis</p>
      <p class="person-role">Director &nbsp;|&nbsp; Senior Search Consultant</p>
    </div>
    <div class="divider-vertical"></div>
    <ul class="contacts">
      <li><span class="label">T:</span> +64 27 480 2291</li>
      <li><span class="label">E:</span> claire@mapleroster.nz</li>
      <li><span class="label">W:</span> www.mapleroster.nz</li>
    </ul>
    <div class="divider-horizontal"></div>
    <p class="location">Auckland, New Zealand</p>
  </section>

  <section class="card card-back" aria-label="Business card back">
    <div class="back-pattern" role="img" aria-label="Faint repeating brand pattern on deep navy"></div>
    <div class="back-brand">
      <span class="brand-name">Maple Roster</span>
    </div>
  </section>
</main>
</body>
</html>
```